International service dog training school needs web design

We need to upgrade our website. The website is https://brightmeadow.studio/
We help trainers and service dog programs learn how to train service dogs with the latest and most ethical training methods. We offer online and in-person coaching services. We would like to see designs that are engaging and communicate professionalism, expertise, and care for the dogs and people we work with. Please also keep the colors already in the logo in the design.

```html
<!DOCTYPE html>
<html lang="en">
<head>
<meta charset="utf-8">
<title>Miriam Holloway Ph.D. – Coaching for Service Dog Professionals</title>
<link rel="stylesheet" href="https://fonts.googleapis.com/css2?family=Lato:wght@400;700;900&display=swap">
<style>
:root{
  --teal:#1a9886;
  --teal-dark:#137a6c;
  --blue:#1e5cae;
  --ink:#1f1f1f;
  --text:#3a3a3a;
  --grey:#efefef;
  --white:#ffffff;
}
*{box-sizing:border-box;margin:0;padding:0}
html,body{width:1200px;height:5195px;overflow:hidden}
body{position:relative;font-family:'Lato',sans-serif;color:var(--text);background:var(--white)}
.abs{position:absolute}
.btn{position:absolute;display:flex;align-items:center;justify-content:center;background:var(--teal);color:var(--white);font-weight:700;font-size:16px;letter-spacing:.3px;text-decoration:none;height:48px}
.photo{position:absolute;overflow:hidden}
.ring{position:absolute;border-radius:50%;border:12px solid var(--teal);border-left-color:transparent;border-right-color:transparent}
.ring .photo{inset:12px;border-radius:50%}
/* header */
.site-header{position:absolute;left:0;top:0;width:1200px;height:145px;border-top:5px solid var(--blue)}
.brand{position:absolute;left:75px;top:28px;display:flex;align-items:center;gap:16px}
.brand-mark{width:90px;height:90px;border-radius:50%;background:var(--blue)}
.brand-name{font-weight:700;color:var(--blue);font-size:30px;line-height:1.1}
.brand-name small{display:block;font-size:18px;letter-spacing:.5px}
.header-contact{position:absolute;left:765px;top:40px;font-size:24px;color:var(--blue);line-height:42px}
.header-contact div{display:flex;align-items:center;gap:42px}
.header-contact svg{width:20px;height:20px;fill:var(--teal)}
.main-nav{position:absolute;left:0;top:145px;width:1200px;height:73px;background:var(--teal);display:flex;align-items:center;padding-left:110px;gap:51px}
.main-nav a{color:var(--white);font-weight:700;font-size:17px;text-decoration:none}
/* hero */
.hero{position:absolute;left:0;top:218px;width:1200px;height:615px;background:linear-gradient(120deg,#5c6f8a 0%,#4e6a4a 40%,#8a8a55 65%,#b79a62 85%,#6c7a52 100%)}
.hero-title{position:absolute;left:0;width:1200px;top:170px;text-align:center;color:var(--white);font-weight:700;font-size:52px;line-height:60px}
.hero-sub{position:absolute;left:0;width:1200px;top:302px;text-align:center;color:var(--white);font-weight:700;font-size:30px}
.hero .btn{left:525px;top:372px;width:150px;height:46px;background:var(--blue);font-size:16px}
.dots{position:absolute;top:558px;left:550px;display:flex;gap:16px}
.dots span{width:12px;height:12px;border-radius:50%;background:var(--white)}
.dots span:first-child{background:var(--teal)}
/* courses */
.section-title{position:absolute;left:0;width:1200px;text-align:center;font-weight:900;font-size:32px;color:var(--ink)}
.course-label{position:absolute;width:240px;text-align:center;color:var(--blue);font-weight:700;font-size:16px;line-height:26px}
.arrow{position:absolute;width:20px;height:30px}
.arrow path{fill:none;stroke:var(--ink);stroke-width:4}
/* split sections */
.band{position:absolute;left:0;width:1200px;background:var(--grey)}
.band svg.wedges{position:absolute;left:0;top:0}
.h2{position:absolute;font-weight:900;font-size:34px;color:var(--ink)}
.body-copy{position:absolute;width:470px;font-size:15px;line-height:31.5px;color:var(--text)}
/* cards */
.card-photo{position:absolute;width:330px;height:250px}
.card-tag{position:absolute;width:290px;background:var(--white);text-align:center;color:var(--blue);font-weight:700;font-size:18px;line-height:28px;padding-top:14px}
.card-copy{position:absolute;width:270px;text-align:center;font-size:16px;line-height:30px;color:var(--text)}
/* book */
.book-title{position:absolute;left:76px;top:3430px;font-weight:900;font-size:34px;line-height:42px;color:var(--ink)}
.book-sub{position:absolute;left:76px;top:3548px;width:600px;font-size:26px;line-height:42px;color:var(--text)}
/* staying ahead */
.cta{position:absolute;left:0;top:4390px;width:1200px;height:465px;background:linear-gradient(180deg,#1f8f86 0%,#1a9886 50%,#137a6c 100%)}
.cta-title{position:absolute;left:0;width:1200px;top:170px;text-align:center;color:var(--white);font-weight:700;font-size:34px}
.cta-sub{position:absolute;left:340px;width:520px;top:227px;text-align:center;color:var(--white);font-size:21px;line-height:35px}
.cta .btn{left:523px;top:318px;width:152px;height:46px;background:#1b1b1b}
/* footer */
.site-footer{position:absolute;left:0;top:4855px;width:1200px;height:340px;background:var(--white)}
.foot-head{position:absolute;color:var(--blue);font-weight:700;font-size:16px}
.foot-list{position:absolute;font-size:13px;line-height:32px;color:var(--ink)}
.foot-list a{color:var(--ink);text-decoration:none;display:block}
.foot-contact{position:absolute;font-size:13px;line-height:29px;color:var(--ink)}
.foot-contact div{display:flex;align-items:center;gap:20px}
.foot-contact svg{width:12px;height:12px;fill:var(--blue)}
.social{position:absolute;display:flex;gap:21px}
.social span{width:24px;height:24px;border-radius:50%;background:var(--ink)}
.email-field{position:absolute;left:884px;top:87px;width:242px;height:50px;background:#eeeeee;font-size:13px;color:var(--ink);padding:16px 0 0 18px}
.subscribe{position:absolute;left:884px;top:150px;width:242px;height:48px;background:var(--blue);color:var(--white);font-weight:700;font-size:16px;display:flex;align-items:center;justify-content:center}
</style>
</head>
<body>

<header class="site-header">
  <div class="brand">
    <span class="brand-mark"></span>
    <div class="brand-name">Miriam Holloway Ph.D.<small>MEADOWBROOK CENTER FOR ASSISTANCE CANINES</small></div>
  </div>
  <div class="header-contact">
    <div><svg viewBox="0 0 24 24"><path d="M6.6 10.8a15 15 0 0 0 6.6 6.6l2.2-2.2c.3-.3.7-.4 1-.2 1.1.4 2.3.6 3.6.6.6 0 1 .4 1 1V20c0 .6-.4 1-1 1A17 17 0 0 1 3 4c0-.6.4-1 1-1h3.5c.6 0 1 .4 1 1 0 1.3.2 2.5.6 3.6.1.3 0 .7-.2 1z"/></svg>1-800-555-0142</div>
    <div><svg viewBox="0 0 24 24"><path d="M2 5h20v3l-10 6L2 8zm0 5l10 6 10-6v9H2z"/></svg>info@brightmeadow.studio</div>
  </div>
</header>

<nav class="main-nav">
  <a href="#">HOME</a><a href="#">THE CENTER</a><a href="#">HELPING ORGANIZATIONS</a><a href="#">TEACHING TRAINERS</a><a href="#">RESEARCH</a><a href="#">CONTACT</a>
</nav>

<section class="hero" role="img" aria-label="Trainer in a field offering a treat to an attentive golden retriever">
  <h1 class="hero-title">COACHING FOR<br>SERVICE DOG PROFESSIONALS</h1>
  <p class="hero-sub">The Meadowbrook center for assistance canines</p>
  <a class="btn" href="#">READ MORE</a>
  <div class="dots"><span></span><span></span><span></span><span></span></div>
</section>

<h2 class="section-title" style="top:888px">FIND YOUR COURSES</h2>
<svg class="arrow" style="left:44px;top:1100px" viewBox="0 0 20 30"><path d="M16 3 4 15l12 12"/></svg>
<svg class="arrow" style="left:1138px;top:1100px" viewBox="0 0 20 30"><path d="M4 3l12 12L4 27"/></svg>

<div class="ring" style="left:76px;top:982px;width:240px;height:250px"><div class="photo" role="img" aria-label="Dog waiting in a kennel run" style="background:linear-gradient(160deg,#c9c3b4,#8d8a7c)"></div></div>
<div class="ring" style="left:344px;top:982px;width:240px;height:250px"><div class="photo" role="img" aria-label="Trainers attending a classroom assessment session" style="background:linear-gradient(160deg,#b9a894,#5f5248)"></div></div>
<div class="ring" style="left:614px;top:982px;width:240px;height:250px"><div class="photo" role="img" aria-label="Handler practicing a task with a dog indoors" style="background:linear-gradient(160deg,#cfcac3,#6d625a)"></div></div>
<div class="ring" style="left:882px;top:982px;width:240px;height:250px"><div class="photo" role="img" aria-label="Group of trainers walking dogs in a hallway" style="background:linear-gradient(160deg,#d2cfca,#5b5650)"></div></div>

<div class="course-label" style="left:76px;top:1253px">SERVICE DOG CANDIDATE<br>SELECTION</div>
<div class="course-label" style="left:344px;top:1253px">SERVICE DOG TRAINING<br>&amp; ASSESSMENTS</div>
<div class="course-label" style="left:614px;top:1253px">MEDICAL ASSISTANT<br>DOG TASKS</div>
<div class="course-label" style="left:882px;top:1253px">ALL YOU NEED<br>FULL CURRICULUM</div>

<section class="band" style="top:1375px;height:640px">
  <svg class="wedges" width="1200" height="640" viewBox="0 0 1200 640">
    <polygon points="0,0 600,30 0,92" fill="var(--blue)"/>
    <polygon points="0,548 600,610 0,640" fill="var(--blue)"/>
    <polygon points="600,610 1200,640 600,640" fill="#fff"/>
  </svg>
  <h2 class="h2" style="left:75px;top:142px">ABOUT US</h2>
  <p class="body-copy" style="left:75px;top:196px">The Meadowbrook Center for Assistance Canines was founded by Miriam Holloway Ph.D. in response to demand for coaching from dog trainers, medical professionals, and service dog programs. Miriam Holloway Ph.D. has helped hundreds of trainers and several programs both in the US and internationally, expand the type of dogs they could offer to include medical alert dogs.</p>
  <a class="btn" href="#" style="left:75px;top:437px;width:152px">READ MORE</a>
  <div class="ring" style="left:650px;top:70px;width:486px;height:495px"><div class="photo" role="img" aria-label="German shepherd lying on grass beside handlers at a training session" style="background:linear-gradient(160deg,#4a6fa8,#3f5a3a 60%,#6e7d4b)"></div></div>
</section>

<svg class="arrow" style="left:44px;top:2300px" viewBox="0 0 20 30"><path d="M16 3 4 15l12 12"/></svg>
<svg class="arrow" style="left:1138px;top:2300px" viewBox="0 0 20 30"><path d="M4 3l12 12L4 27"/></svg>

<div class="card-photo photo" role="img" aria-label="Group photo of an organization's staff with their dogs" style="left:75px;top:2080px;background:linear-gradient(160deg,#8fa1b8,#7a5a4c)"></div>
<div class="card-tag" style="left:95px;top:2289px">ORGANIZATION/PROGRAM<br>CONSULTING</div>
<p class="card-copy" style="left:105px;top:2370px">Helping organizations get started, improve their training program, and add services.</p>
<a class="btn" href="#" style="left:164px;top:2486px;width:152px">READ MORE</a>

<div class="card-photo photo" role="img" aria-label="Trainer coaching with a dog in an office corridor" style="left:435px;top:2080px;background:linear-gradient(160deg,#b8b2aa,#4d4640)"></div>
<div class="card-tag" style="left:455px;top:2289px">PROFESSIONAL<br>COACHING/TEACHING FOR<br>DOG TRAINERS</div>
<p class="card-copy" style="left:465px;top:2398px">Helping dog trainers improve their skills and learn about service dog training and medical alert dog training.</p>
<a class="btn" href="#" style="left:524px;top:2537px;width:152px">READ MORE</a>

<div class="card-photo photo" role="img" aria-label="Detection dog sniffing a scent container during a study" style="left:795px;top:2080px;background:linear-gradient(160deg,#d8d4cd,#8e8378)"></div>
<div class="card-tag" style="left:815px;top:2289px">COLLABORATING<br>IN RESEARCH PROJECTS</div>
<p class="card-copy" style="left:825px;top:2370px">Collaborating in research studies in the field of Medical Detection Dogs.</p>
<a class="btn" href="#" style="left:884px;top:2486px;width:152px">READ MORE</a>

<section class="band" style="top:2645px;height:640px">
  <svg class="wedges" width="1200" height="640" viewBox="0 0 1200 640">
    <polygon points="1200,0 1200,92 600,48" fill="var(--blue)"/>
    <polygon points="1200,560 600,600 1200,640" fill="var(--blue)"/>
    <polygon points="0,640 600,600 600,640" fill="#fff"/>
  </svg>
  <div class="ring" style="left:75px;top:70px;width:466px;height:505px"><div class="photo" role="img" aria-label="Curly-haired dog resting its paws on a laptop during a video call" style="background:linear-gradient(160deg,#7d7a74,#a75a2e 60%,#c07a48)"></div></div>
  <h2 class="h2" style="left:613px;top:145px">ONLINE COACHING SERVICES</h2>
  <p class="body-copy" style="left:613px;top:200px;width:520px">The Meadowbrook Center for Assistance Canines was founded by Miriam Holloway Ph.D. in response to demand for coaching from dog trainers, medical professionals, and service dog programs. Miriam Holloway Ph.D. has helped hundreds of trainers and several programs both in the US and internationally, expand the type of dogs they could offer to include medical alert dogs.</p>
  <a class="btn" href="#" style="left:613px;top:442px;width:152px">READ MORE</a>
</section>

<h2 class="book-title">NEW BOOK FROM MIRIAM<br>HOLLOWAY PH.D.!</h2>
<p class="book-sub">Choosing And Preparing Your Service Dog: A Guide to Public Access Work</p>
<a class="btn" href="#" style="left:76px;top:3650px;width:152px">READ MORE</a>
<div class="photo" role="img" aria-label="Book cover showing a golden retriever in a red service vest" style="left:728px;top:3345px;width:290px;height:445px;background:linear-gradient(180deg,#f4f1ec 0%,#e9e3da 55%,#b5262a 80%,#8f1c1f 100%);box-shadow:6px 6px 10px rgba(0,0,0,.25)"></div>

<section class="band" style="top:3835px;height:555px">
  <svg class="wedges" width="1200" height="555" viewBox="0 0 1200 555">
    <polygon points="0,0 600,30 0,90" fill="var(--blue)"/>
  </svg>
  <h2 class="h2" style="left:75px;top:145px">IN-PERSON COACHING SERVICES</h2>
  <p class="body-copy" style="left:75px;top:200px">The Meadowbrook Center for Assistance Canines was founded by Miriam Holloway Ph.D. in response to demand for coaching from dog trainers, medical professionals, and service dog programs. Miriam Holloway Ph.D. has helped hundreds of trainers and several programs both in the US and internationally, expand the type of dogs they could offer to include medical alert dogs.</p>
  <a class="btn" href="#" style="left:75px;top:442px;width:152px">READ MORE</a>
  <div class="ring" style="left:650px;top:70px;width:486px;height:455px"><div class="photo" role="img" aria-label="Golden retriever on a leash during an outdoor group session" style="background:linear-gradient(160deg,#8f8a80,#5b5a52 50%,#b0a690)"></div></div>
</section>

<section class="cta" role="img" aria-label="Handlers standing with their dogs, tinted in teal">
  <svg class="wedges abs" style="left:0;top:0" width="1200" height="90" viewBox="0 0 1200 90">
    <polygon points="0,0 0,85 600,45" fill="var(--blue)"/>
  </svg>
  <h2 class="cta-title">STAYING AHEAD</h2>
  <p class="cta-sub">Science-based and ethical training methods for the modern service dog trainer.</p>
  <a class="btn" href="#">GET STARTED</a>
</section>

<footer class="site-footer">
  <span class="abs" style="left:75px;top:55px;width:130px;height:130px;border-radius:50%;background:var(--blue)"></span>
  <p class="abs" style="left:75px;top:187px;font-size:13px;line-height:20px;color:var(--ink)">Copyright © 2021. Bright Meadow<br>All Right Reserved</p>

  <h3 class="foot-head" style="left:350px;top:52px">SITE MAP</h3>
  <div class="foot-list" style="left:350px;top:80px">
    <a href="#">Home</a><a href="#">The Center</a><a href="#">Helping organizations</a><a href="#">Teaching Trainers</a><a href="#">Research</a><a href="#">Contact</a>
  </div>

  <h3 class="foot-head" style="left:575px;top:52px">CONTACT US</h3>
  <div class="foot-contact" style="left:575px;top:80px">
    <div><svg viewBox="0 0 24 24"><path d="M6.6 10.8a15 15 0 0 0 6.6 6.6l2.2-2.2c.3-.3.7-.4 1-.2 1.1.4 2.3.6 3.6.6.6 0 1 .4 1 1V20c0 .6-.4 1-1 1A17 17 0 0 1 3 4c0-.6.4-1 1-1h3.5c.6 0 1 .4 1 1 0 1.3.2 2.5.6 3.6.1.3 0 .7-.2 1z"/></svg>1-800-555-0142</div>
    <div><svg viewBox="0 0 24 24"><path d="M2 5h20v3l-10 6L2 8zm0 5l10 6 10-6v9H2z"/></svg>info@brightmeadow.studio</div>
    <div style="color:var(--teal);font-weight:700">Map Location</div>
  </div>
  <div class="social" style="left:575px;top:184px"><span></span><span></span><span></span><span></span><span></span></div>

  <h3 class="foot-head" style="left:884px;top:52px">EMAIL US</h3>
  <div class="email-field">Email Address</div>
  <div class="subscribe">SUBSCRIBE</div>
</footer>

</body>
</html>
```